Mindfulness School for Children -- Business Cards

We're looking for business cards for our school directors and owners. We're a mindfulness school for children called little lanterns. Attached are our logos/icons.

```html
<!DOCTYPE html>
<html lang="en">
<head>
<meta charset="utf-8">
<title>Little Lanterns — Business Cards</title>
<link rel="stylesheet" href="https://fonts.googleapis.com/css2?family=Source+Sans+3:wght@300;400;600;700&display=swap">
<style>
  :root {
    --stage: #1c1d1f;
    --card-white: #fbfbfa;
    --teal: #3a9fb5;
    --teal-light: #78c4c9;
    --teal-deep: #2a7183;
    --teal-back-a: #74bfcb;
    --teal-back-b: #3e8fa1;
    --teal-back-c: #2a6f80;
    --ink: #5b5f62;
    --rule: #c9cccd;
    --white: #ffffff;
  }
  * { margin: 0; padding: 0; box-sizing: border-box; }
  html, body { width: 1200px; height: 900px; overflow: hidden; }
  body {
    background: var(--stage);
    font-family: "Source Sans 3", sans-serif;
    display: flex;
    align-items: center;
    justify-content: center;
    gap: 40px;
  }
  .card {
    width: 525px;
    height: 300px;
    position: relative;
    border-radius: 2px;
    overflow: hidden;
    box-shadow: 0 10px 30px rgba(0, 0, 0, 0.5);
  }

  /* Front */
  .card-front { background: var(--card-white); color: var(--ink); }
  .wordmark {
    position: absolute;
    top: 58px;
    left: 0;
    right: 0;
    display: flex;
    align-items: center;
    justify-content: center;
    gap: 12px;
    font-size: 46px;
    font-weight: 400;
    letter-spacing: 0.5px;
    color: var(--teal-light);
  }
  .wordmark-dot {
    width: 14px;
    height: 14px;
    border-radius: 50%;
    background: var(--teal-light);
  }
  .details {
    position: absolute;
    left: 48px;
    right: 36px;
    top: 168px;
    display: flex;
    align-items: stretch;
  }
  .person { width: 200px; padding-right: 18px; }
  .person-name {
    font-weight: 700;
    font-size: 15px;
    letter-spacing: 0.3px;
    color: var(--teal);
    text-transform: uppercase;
  }
  .person-role {
    font-weight: 400;
    font-size: 12.5px;
    color: var(--teal-light);
    margin-bottom: 3px;
  }
  .address { font-size: 12.5px; line-height: 1.3; }
  .divider { width: 1px; background: var(--rule); margin: 2px 0; }
  .contact { padding-left: 18px; font-size: 12.5px; line-height: 1.35; }
  .company { font-weight: 700; font-size: 13px; color: var(--teal); margin-bottom: 1px; }
  .contact-line { display: flex; align-items: center; gap: 6px; }
  .contact-line svg { width: 11px; height: 11px; flex: none; fill: var(--teal); }

  /* Back */
  .card-back { background: var(--teal-back-b); }
  .back-pattern {
    position: absolute;
    inset: 0;
    background:
      radial-gradient(ellipse at 70% 30%, var(--teal-back-a) 0%, transparent 60%),
      linear-gradient(160deg, var(--teal-back-b) 0%, var(--teal-back-a) 55%, var(--teal-back-c) 100%);
  }
  .back-mark {
    position: absolute;
    left: 0;
    right: 0;
    top: 50%;
    transform: translateY(-50%);
    display: flex;
    align-items: center;
    justify-content: center;
    gap: 14px;
    font-size: 40px;
    font-weight: 400;
    color: var(--white);
  }
  .back-dot {
    width: 14px;
    height: 14px;
    border-radius: 50%;
    background: var(--white);
  }
</style>
</head>
<body>

  <section class="card card-front" aria-label="Business card front">
    <div class="wordmark"><span>little lanterns</span><span class="wordmark-dot"></span></div>

    <div class="details">
      <div class="person">
        <div class="person-name">Clara Whitfield</div>
        <div class="person-role">Managing Director</div>
        <div class="address">2250 Willow Lane Fairview<br>OR 97024, United States</div>
      </div>
      <div class="divider"></div>
      <div class="contact">
        <div class="company">Little Lanterns</div>
        <div class="contact-line">
          <svg viewBox="0 0 24 24" aria-hidden="true"><path d="M6.6 10.8a15.1 15.1 0 0 0 6.6 6.6l2.2-2.2a1 1 0 0 1 1-.25 11.4 11.4 0 0 0 3.6.57 1 1 0 0 1 1 1V20a1 1 0 0 1-1 1A17 17 0 0 1 3 4a1 1 0 0 1 1-1h3.5a1 1 0 0 1 1 1c0 1.25.2 2.45.57 3.57a1 1 0 0 1-.25 1z"/></svg>
          <span>(+1) 555.014.2200</span>
        </div>
        <div class="contact-line">
          <svg viewBox="0 0 24 24" aria-hidden="true"><path d="M2 5h20L12 13z"/><path d="M2 7l10 8 10-8v12H2z"/></svg>
          <span>info@littlelanterns.org</span>
        </div>
        <div class="contact-line">
          <svg viewBox="0 0 24 24" aria-hidden="true"><circle cx="12" cy="12" r="10"/><path d="M2 12h20M12 2c3 3 3 17 0 20M12 2c-3 3-3 17 0 20" stroke="#fbfbfa" stroke-width="1.4" fill="none"/></svg>
          <span>www.littlelanterns.org</span>
        </div>
      </div>
    </div>
  </section>

  <section class="card card-back" aria-label="Business card back">
    <div class="back-pattern" role="img" aria-label="Repeating embossed flower pattern in light and deep teal tones"></div>
    <div class="back-mark"><span class="back-dot"></span><span>little lanterns</span></div>
  </section>

</body>
</html>
```